New Business Card (to reflect updated website content and graphics)

I changed some text and graphics on my website, so I need a new business card.

Target Market(s)

Mostly women, ages 30 - 60.

Industry/Entity Type

Life Coaching

Contact Information for Business Card

Included in attached Word document

Font styles to use
Sans Serif

Requirements
Must have
• I am not a creative person, so I will defer to designer. Take a look at my website, and you can get a feel for me, my style, and my target audience. Thank You!

My 3 branding colors are included in attached Word document.

```html
<!DOCTYPE html>
<html lang="en">
<head>
<meta charset="utf-8">
<title>Willow Path Coaching – Business Card</title>
<link rel="stylesheet" href="https://fonts.googleapis.com/css2?family=Lora:wght@400;700&display=swap">
<style>
  :root {
    --backdrop: #2b2b2b;
    --card-white: #ffffff;
    --brand-teal: #2594b0;
    --brand-deep-teal: #1f7f99;
    --brand-coral: #f27a6a;
    --ink-light: #ffffff;
    --shadow: rgba(0, 0, 0, 0.45);
  }
  * { margin: 0; padding: 0; box-sizing: border-box; }
  html, body {
    width: 1200px;
    height: 900px;
    overflow: hidden;
    background: var(--backdrop);
  }
  .canvas {
    width: 1200px;
    height: 900px;
    display: flex;
    flex-direction: column;
    align-items: center;
    justify-content: center;
    gap: 40px;
  }
  .card {
    width: 600px;
    height: 343px;
    position: relative;
    box-shadow: 0 12px 30px var(--shadow);
    overflow: hidden;
  }
  /* Front side */
  .card--front {
    background: var(--card-white);
  }
  .word-cloud {
    position: absolute;
    left: 50%;
    top: 46%;
    width: 250px;
    height: 210px;
    transform: translate(-50%, -50%);
    border-radius: 6px;
    background: linear-gradient(135deg, var(--brand-deep-teal) 0%, #5aa9bf 55%, #e99c91 100%);
    opacity: 0.9;
  }
  /* Back side */
  .card--back {
    background: var(--brand-teal);
    color: var(--ink-light);
    font-family: "Lora", Georgia, serif;
  }
  .brand {
    position: absolute;
    right: 48px;
    top: 62px;
    display: flex;
    align-items: center;
    gap: 10px;
  }
  .brand__dot {
    width: 12px;
    height: 12px;
    border-radius: 50%;
    background: var(--ink-light);
  }
  .brand__name {
    font-family: "Lora", Georgia, serif;
    font-weight: 400;
    font-size: 24px;
    letter-spacing: 1px;
    color: var(--ink-light);
  }
  .contact {
    position: absolute;
    left: 48px;
    bottom: 36px;
  }
  .contact__name {
    font-weight: 700;
    font-size: 20px;
    letter-spacing: 1px;
    text-transform: uppercase;
    line-height: 1.2;
  }
  .contact__titles {
    font-size: 15px;
    line-height: 1.3;
    margin-bottom: 16px;
  }
  .contact__list {
    list-style: none;
    font-size: 15px;
    line-height: 1.45;
  }
  .contact__item {
    display: flex;
    align-items: center;
    gap: 10px;
  }
  .contact__icon {
    width: 13px;
    height: 13px;
    flex: none;
  }
</style>
</head>
<body>
<main class="canvas">

  <section class="card card--front" aria-label="Card front">
    <div class="word-cloud" role="img"
         aria-label="Heart-shaped word cloud of coaching themes such as hope, joy, love, clarity and peace, with the motto Feel Better, Live Well"></div>
  </section>

  <section class="card card--back" aria-label="Card back">
    <div class="brand">
      <span class="brand__dot"></span>
      <span class="brand__name">Willow Path Coaching</span>
    </div>

    <div class="contact">
      <p class="contact__name">Dana Merriwell</p>
      <p class="contact__titles">
        Certified Professional Life Coach<br>
        Health &amp; Wellness Coach<br>
        Advanced Grief Support Specialist
      </p>
      <ul class="contact__list">
        <li class="contact__item">
          <svg class="contact__icon" viewBox="0 0 16 16" aria-hidden="true">
            <path d="M3 1 L6 1 L7 5 L5 6.5 C6 9 7 10 9.5 11 L11 9 L15 10 L15 13 C15 14 14 15 13 15 C6 15 1 10 1 3 C1 2 2 1 3 1 Z" fill="currentColor"/>
          </svg>
          <span>(555) 214-0387</span>
        </li>
        <li class="contact__item">
          <svg class="contact__icon" viewBox="0 0 16 16" aria-hidden="true">
            <rect x="1" y="3" width="14" height="10" fill="currentColor"/>
            <path d="M1 3 L8 9 L15 3" fill="none" stroke="#2594b0" stroke-width="1.4"/>
          </svg>
          <span>dana@willowpathcoaching.com</span>
        </li>
        <li class="contact__item">
          <svg class="contact__icon" viewBox="0 0 16 16" aria-hidden="true">
            <circle cx="8" cy="8" r="7" fill="none" stroke="currentColor" stroke-width="1.4"/>
            <ellipse cx="8" cy="8" rx="3" ry="7" fill="none" stroke="currentColor" stroke-width="1.2"/>
            <line x1="1" y1="8" x2="15" y2="8" stroke="currentColor" stroke-width="1.2"/>
          </svg>
          <span>www.willowpathcoaching.com</span>
        </li>
      </ul>
    </div>
  </section>

</main>
</body>
</html>
```